Bold Flyer Needed for Bold Little Gym

We need a 1 page flyer created for our small boutique fitness facility, CorVanto, which highlights a new service we are offering.
We are now offering Red Light Therapy (RLT) to our members and I need a full color, 1 page flyer created that captures the eye of our members while highlighting the benefits and clearly stating the prices at the bottom of the page.
Flyer will be printed out on a standard 8.5" x 11" sheet of paper and should be laid out in a way that is easy to read. Landscape or Portrait layouts are both expectable.
We are using Silverline Glow Therapy Lights LumaCore 700 Lamps as found here http://lnk.example/7QWRT5Z
I have attached the text that should be included and our logo for branding of the flyer.
Thank you!

```html
<!DOCTYPE html>
<html lang="en">
<head>
<meta charset="utf-8">
<title>CorVanto Red Light Therapy Flyer</title>
<link href="https://fonts.googleapis.com/css2?family=Oswald:wght@600;700&family=Montserrat:wght@700;800&family=Lato:wght@400;700&display=swap" rel="stylesheet">
<style>
:root{
  --ink:#111;
  --panel:#2a2a2a;
  --panel-dark:#0f0f0f;
  --yellow:#f9d103;
  --yellow-soft:#fbe36b;
  --red-deep:#7c0003;
  --red-hot:#e8122e;
  --white:#fff;
  --text:#222;
}
*{margin:0;padding:0;box-sizing:border-box}
html,body{width:927px;height:1200px;overflow:hidden;background:var(--white)}
.flyer{position:relative;width:927px;height:1200px;font-family:'Lato',sans-serif;color:var(--text);overflow:hidden}

/* left sidebar */
.sidebar{position:absolute;left:23px;top:0;width:229px;height:1200px;background:var(--panel)}
.brand{height:89px;background:var(--panel-dark);display:flex;flex-direction:column;align-items:center;justify-content:center}
.brand-name{font-family:'Oswald',sans-serif;font-weight:700;font-size:40px;color:var(--yellow);line-height:1;letter-spacing:1px}
.brand-tag{font-family:'Montserrat',sans-serif;font-weight:700;font-size:7px;letter-spacing:1.4px;color:var(--yellow);margin-top:6px}
.benefits-title{position:absolute;left:11px;top:100px;font-family:'Oswald',sans-serif;font-weight:600;font-size:22px;color:var(--yellow)}
.benefits-rule{position:absolute;left:126px;top:116px;width:103px;height:1px;background:var(--yellow)}
.benefits-rule::before{content:"";position:absolute;left:-3px;top:-3px;width:7px;height:7px;border-radius:50%;background:var(--yellow)}
.top-rule{position:absolute;left:0;top:146px;width:229px;height:1px;background:#444}
.benefit{position:absolute;left:11px;width:207px;border-bottom:1px solid #555}
.benefit h3{font-family:'Montserrat',sans-serif;font-weight:800;font-size:16px;line-height:24px;color:var(--white);border-left:4px solid var(--white);padding-left:7px;width:160px}
.benefit p{font-size:12.5px;line-height:20px;color:var(--white);margin-top:14px}
.benefit svg{position:absolute;right:0;top:0}
.contact-band{position:absolute;left:0;top:1020px;width:252px;height:180px;background:var(--yellow)}
.contact-title{position:absolute;left:23px;top:1072px;width:229px;text-align:center;font-family:'Oswald',sans-serif;font-weight:700;font-size:19px;color:var(--ink)}
.contact-rule{position:absolute;left:0;top:1108px;width:252px;height:1px;background:#6b5a00}
.contact-phone{position:absolute;left:38px;top:1132px}
.contact-label{position:absolute;left:86px;top:1126px;font-family:'Montserrat',sans-serif;font-weight:700;font-size:15px;line-height:27px;color:var(--ink)}

/* header */
.hero-photo{position:absolute;left:252px;top:0;width:675px;height:406px;background:linear-gradient(90deg,#ff1e3c 0%,#d10a22 35%,var(--red-deep) 55%,#8a0508 85%,#e6e2e2 100%)}
.hero-title{position:absolute;left:601px;top:18px;font-family:'Oswald',sans-serif;font-weight:700;font-size:38px;line-height:45.5px;color:var(--white);letter-spacing:1px}
.hero-sub{position:absolute;left:600px;top:292px;font-size:16px;line-height:27px;color:var(--white)}
.intro-band{position:absolute;left:252px;top:378px;width:493px;height:28px;background:var(--white);clip-path:polygon(0 0,96% 0,100% 100%,0 100%)}
.intro-head{position:absolute;left:268px;top:387px;font-family:'Montserrat',sans-serif;font-weight:700;font-size:14.5px;color:var(--ink)}
.intro-copy{position:absolute;left:268px;top:413px;width:625px;font-size:12.3px;line-height:21.3px;color:var(--text)}
.intro-copy b{color:var(--ink)}

/* offer */
.offer-head{position:absolute;left:268px;top:509px;font-family:'Montserrat',sans-serif;font-weight:700;font-size:18px;color:var(--ink)}
.offer-banner{position:absolute;left:252px;top:542px;width:400px;height:32px;background:linear-gradient(90deg,var(--yellow) 0%,#c9a90a 45%,#3b3a2a 100%);clip-path:polygon(0 0,97% 0,100% 50%,97% 100%,0 100%)}
.offer-text{position:absolute;left:269px;top:547px;font-weight:700;font-size:15.5px;color:var(--white);white-space:pre}
.limited{position:absolute;left:268px;top:593px;font-size:15px;color:var(--ink)}
.limited-note{position:absolute;left:269px;top:623px;font-size:9.8px;color:var(--text)}
.ready{position:absolute;left:269px;top:648px;font-size:15px;color:var(--ink)}
.cta{position:absolute;left:269px;top:677px;font-size:15px;line-height:24px;color:var(--ink)}
.cta svg{vertical-align:-4px;margin:0 4px 0 6px}
.motto{position:absolute;left:268px;top:732px;font-weight:700;font-size:12px;color:var(--ink)}

/* middle photo */
.session-photo{position:absolute;left:252px;top:764px;width:453px;height:171px;background:linear-gradient(180deg,#e8203e 0%,#b30f22 55%,#4a0309 100%)}

/* pricing */
.pricing-head{position:absolute;left:268px;top:952px;font-size:15px;color:var(--ink)}
.price-table{position:absolute;left:270px;top:983px;width:415px;height:193px;border:3px solid var(--yellow);border-collapse:collapse;background:linear-gradient(180deg,#3d1215,#5a2a2c);color:var(--white);font-size:11px;text-align:center}
.price-table th{background:#1a0a0b;height:33px;font-weight:700;font-size:12px}
.price-table td{height:36px;font-weight:700}
.price-table th+th,.price-table td+td{border-left:1px solid #6a4a4c}

/* why choose */
.why{position:absolute;left:705px;top:485px;width:210px;height:715px;background:var(--yellow);clip-path:polygon(0 28px,50% 0,100% 28px,100% 100%,0 100%)}
.why-cap{position:absolute;left:705px;top:485px;width:210px;height:40px;background:var(--yellow-soft);clip-path:polygon(0 28px,50% 0,100% 28px,100% 40px,50% 12px,0 40px)}
.why-title{position:absolute;left:705px;top:524px;width:210px;text-align:center;font-family:'Oswald',sans-serif;font-weight:600;font-size:21px;color:var(--ink)}
.diamond{position:absolute;left:714px;width:192px;height:192px}
.diamond svg{position:absolute;left:0;top:0}
.diamond-text{position:absolute;left:26px;width:140px;text-align:center;color:var(--white)}
.diamond-text h4{font-size:15px;line-height:21px;font-weight:400}
.diamond-text p{font-size:10.5px;line-height:18px;margin-top:4px}
</style>
</head>
<body>
<div class="flyer">

  <aside class="sidebar">
    <div class="brand">
      <div class="brand-name">CorVanto</div>
      <div class="brand-tag">PERSONAL GROUP TRAINING</div>
    </div>
    <div class="benefits-title">Our Benefits</div>
    <div class="benefits-rule"></div>
    <div class="top-rule"></div>

    <div class="benefit" style="top:168px;height:124px">
      <h3>BOOSTS ENERGY LEVELS</h3>
      <svg width="42" height="44" viewBox="0 0 42 44"><path d="M8 14h16l3 8-6 10v10h-9V30l-5-8z" fill="var(--yellow)"/><circle cx="36" cy="22" r="5" fill="var(--yellow)"/><path d="M16 2v6M8 5l3 5M24 5l-3 5" stroke="var(--yellow)" stroke-width="2"/></svg>
      <p>Feel revitalized and more energetic after each session.</p>
    </div>

    <div class="benefit" style="top:310px;height:126px">
      <h3>ENHANCES MUSCLE RECOVERY</h3>
      <svg width="42" height="60" viewBox="0 0 42 60"><rect x="1" y="22" width="8" height="20" rx="3" fill="var(--yellow)"/><rect x="33" y="22" width="8" height="20" rx="3" fill="var(--yellow)"/><rect x="10" y="26" width="22" height="12" rx="3" fill="var(--yellow)"/><circle cx="21" cy="22" r="6" fill="var(--yellow)"/></svg>
      <p>Speed up recovery times post -workout and reduce</p>
    </div>

    <div class="benefit" style="top:460px;height:122px">
      <h3>IMPROVES SKIN HEALTH</h3>
      <svg width="42" height="42" viewBox="0 0 42 42"><path d="M27 2l2 6 6 2-6 2-2 6-2-6-6-2 6-2z M10 4v8M6 8h8" fill="var(--yellow)" stroke="var(--yellow)" stroke-width="2"/><rect x="0" y="22" width="42" height="6" fill="var(--yellow)"/><path d="M0 36q5-5 10 0t10 0 10 0 12 0" stroke="var(--yellow)" stroke-width="3" fill="none"/></svg>
      <p>Reduce wrinkles, blemishes, and promote a youthful glow.</p>
    </div>

    <div class="benefit" style="top:612px;height:116px">
      <h3>SUPPORTS JOINT HEALTH</h3>
      <svg width="42" height="48" viewBox="0 0 42 48"><circle cx="24" cy="16" r="9" fill="var(--yellow)"/><circle cx="16" cy="30" r="8" fill="var(--yellow)"/><path d="M12 34l-8 12" stroke="var(--yellow)" stroke-width="6"/><circle cx="34" cy="34" r="7" fill="var(--yellow)"/><path d="M34 30v8M30 34h8" stroke="var(--panel)" stroke-width="2"/></svg>
      <p>Alleviate pain and inflammation, making movement easier.</p>
    </div>

    <div class="benefit" style="top:752px;height:120px">
      <h3>PROMOTES BETTER SLEEP</h3>
      <svg width="42" height="46" viewBox="0 0 42 46"><path d="M20 8a18 18 0 1 0 20 22 14 14 0 0 1-20-22z" fill="var(--yellow)"/><path d="M26 6h6l-6 7h6M34 0h6l-6 7h6" stroke="var(--yellow)" stroke-width="2" fill="none"/></svg>
      <p>Improve your sleep patterns and overall restfulness.</p>
    </div>

    <div class="benefit" style="top:903px;height:110px;border-bottom:none">
      <h3>INCREASES CIRCULATION</h3>
      <svg width="42" height="48" viewBox="0 0 42 48"><circle cx="24" cy="16" r="9" fill="var(--yellow)"/><circle cx="16" cy="30" r="8" fill="var(--yellow)"/><path d="M12 34l-8 12" stroke="var(--yellow)" stroke-width="6"/><circle cx="34" cy="34" r="7" fill="var(--yellow)"/><path d="M34 30v8M30 34h8" stroke="var(--panel)" stroke-width="2"/></svg>
      <p>Enhance blood flow for better nutrient delivery to muscles.</p>
    </div>
  </aside>

  <div class="contact-band"></div>
  <svg style="position:absolute;left:0;top:1016px" width="252" height="62" viewBox="0 0 252 62"><polygon points="23,0 252,0 252,62 23,14" fill="var(--panel)"/><polygon points="0,12 23,14 23,0 0,8" fill="var(--yellow)"/></svg>
  <div class="contact-title">CONTACT US</div>
  <div class="contact-rule"></div>
  <svg class="contact-phone" width="40" height="40" viewBox="0 0 40 40"><circle cx="20" cy="20" r="20" fill="var(--ink)"/><path d="M13 11l5 5-3 3q2 4 6 6l3-3 5 5-3 3q-10 0-16-13z" fill="var(--yellow)"/></svg>
  <div class="contact-label">Call Us:<br>(555) 214-3098</div>

  <div class="hero-photo" role="img" aria-label="Photo of a woman relaxing in front of glowing red light therapy panels, with a tall light panel on the right"></div>
  <h1 class="hero-title">UNLOCK YOUR<br>POTENTIAL<br>WITH RED<br>LIGHT<br>THERAPY<br>AT CORVANTO!</h1>
  <p class="hero-sub">Introducing Our New<br>Red Light Therapy Room!</p>
  <div class="intro-band"></div>
  <h2 class="intro-head">Transform Your Wellness Routine with the Power of Light!</h2>
  <p class="intro-copy"><b>What is Red Light Therapy?</b>&nbsp; Red Light Therapy (RLT) is a revolutionary treatment that uses specific wavelengths of light to promote healing, reduce inflammation, and enhance overall well-being. At CorVanto, we are excited to offer the advanced Silverline Glow Therapy LumaCore 700 panels—designed to maximize your health benefits in a relaxing environment.</p>

  <h2 class="offer-head">Special Introductory Offer!</h2>
  <div class="offer-banner"></div>
  <div class="offer-text">Try Your First Session for Just $25!      (Regularly $55)</div>
  <p class="limited">Limited Time Only!</p>
  <p class="limited-note">Book your session today and discover how Red Light Therapy can elevate your fitness journey.</p>
  <p class="ready">READY TO SHINE?</p>
  <p class="cta">Visit our front desk&nbsp; or<svg width="20" height="20" viewBox="0 0 40 40"><circle cx="20" cy="20" r="20" fill="var(--ink)"/><path d="M13 11l5 5-3 3q2 4 6 6l3-3 5 5-3 3q-10 0-16-13z" fill="var(--white)"/></svg>Call us at (555) 214-3098 to<br>Schedule your appointment</p>
  <p class="motto">CorVanto Fitness Facility, Your Wellness, Our Commitment!</p>

  <div class="session-photo" role="img" aria-label="Photo of a man lying on the floor bathed in red therapy light"></div>

  <p class="pricing-head">PRICING</p>
  <table class="price-table">
    <tr><th>PRICES</th><th>CorVanto Member</th><th>Non-Member</th></tr>
    <tr><td>Single Session</td><td>$35</td><td>$55</td></tr>
    <tr><td>3-Pack</td><td>$102</td><td>$159</td></tr>
    <tr><td>5-Pack</td><td>$167</td><td>$259</td></tr>
    <tr><td>10-Pack</td><td>$316</td><td>$491</td></tr>
  </table>

  <div class="why"></div>
  <div class="why-cap"></div>
  <h2 class="why-title">Why Choose CorVanto?</h2>

  <div class="diamond" style="top:569px">
    <svg width="192" height="192" viewBox="0 0 192 192"><path d="M96 0L192 96 96 192 0 96z" fill="var(--panel)" stroke-linejoin="round" stroke="var(--panel)" stroke-width="8"/></svg>
    <div class="diamond-text" style="top:22px"><h4>State-of<br>-the-Art<br>Equipment</h4><p>Experience the power of eight Silverline Glow Therapy LumaCore 700 panels—some of the best on the market!</p></div>
  </div>
  <div class="diamond" style="top:781px">
    <svg width="192" height="192" viewBox="0 0 192 192"><path d="M96 0L192 96 96 192 0 96z" fill="var(--panel)" stroke-linejoin="round" stroke="var(--panel)" stroke-width="8"/></svg>
    <div class="diamond-text" style="top:30px"><h4>Expert<br>Guidance</h4><p>Our trained staff will guide you through each session to ensure you get the most out of your therapy.</p></div>
  </div>
  <div class="diamond" style="top:993px">
    <svg width="192" height="192" viewBox="0 0 192 192"><path d="M96 0L192 96 96 192 0 96z" fill="var(--panel)" stroke-linejoin="round" stroke="var(--panel)" stroke-width="8"/></svg>
    <div class="diamond-text" style="top:42px"><h4>Community<br>Focused</h4><p>Join a supportive community that prioritizes health and wellness.</p></div>
  </div>

</div>
</body>
</html>
```